Need Web Design for Business Process Outsourcing Company (Quorvane)

Quorvane is a business process outsourcing company. Need a simple site similar to http://www.tallowbrinkhire.com/ but with a more professional and credible look. New to the process; not sure where to start and comparing my options. Please let me know what my options are if I choose to go with you. Logo is attached for your reference. Please use same colorway

Reason: I want the final product to be coded. Please confirm you will be able to code final design.

Industry/Entity Type

Business

Coding

Coded - Design and coding required

```html
<!DOCTYPE html>
<html lang="en">
<head>
<meta charset="utf-8">
<title>Quorvane Services</title>
<link href="https://fonts.googleapis.com/css2?family=Roboto:wght@400;500;700&family=Open+Sans:wght@400;600&display=swap" rel="stylesheet">
<style>
:root{
  --navy:#1a4f7e;
  --navy-deep:#1b4a78;
  --sky:#1fb3f2;
  --sky-soft:#4cc3f6;
  --ink:#333b45;
  --muted:#6f7780;
  --pale:#f4f5f7;
  --line:#dcdfe3;
  --white:#ffffff;
}
*{margin:0;padding:0;box-sizing:border-box}
html,body{width:1200px;height:2970px;overflow:hidden;background:var(--white)}
body{font-family:'Roboto',Arial,sans-serif;color:var(--ink);position:relative}
.site-header{position:absolute;left:0;top:0;width:1200px;height:95px;background:var(--white)}
.brand{position:absolute;display:flex;align-items:center;gap:10px;font-family:'Roboto',sans-serif;font-weight:700;color:var(--navy)}
.brand-mark{background:var(--navy)}
.site-header .brand{left:88px;top:26px;font-size:30px}
.site-header .brand-mark{width:36px;height:36px}
.main-nav{position:absolute;top:38px;left:0;width:1200px;font-size:13px;font-weight:500;color:#444;text-transform:uppercase}
.main-nav span{position:absolute}
.main-nav .active{color:var(--sky)}
.hero{position:absolute;left:0;top:95px}
.section-title{position:absolute;left:0;width:1200px;text-align:center;font-size:25px;font-weight:700;color:var(--navy)}
.section-title em,.welcome-title em{font-style:normal;color:var(--sky)}
.lead{position:absolute;left:250px;width:700px;text-align:center;font-size:12.5px;line-height:25px;color:var(--muted)}
.service{position:absolute;width:240px;text-align:center}
.service svg{display:block;margin:0 auto}
.service h3{font-size:15px;font-weight:500;color:#222;margin-top:14px;text-transform:uppercase}
.service p{font-size:12px;line-height:23px;color:var(--muted);margin-top:10px}
.welcome{position:absolute;left:0;top:1200px;width:1200px;height:388px;background:var(--pale)}
.welcome-title{position:absolute;left:88px;top:38px;font-size:25px;font-weight:700;color:var(--navy)}
.welcome-text{position:absolute;left:88px;top:88px;width:520px;font-size:12px;line-height:23px;color:#555}
.welcome-text p+p{margin-top:14px}
.devices{position:absolute;left:715px;top:30px;width:400px;height:330px;border-radius:6px;background:linear-gradient(135deg,#e4e7ea,#a7afb8 55%,#3a4450)}
.projects{position:absolute;left:0;top:1588px;width:1200px;height:356px;background:linear-gradient(120deg,#54c9f8,#22a9ec 60%,#1798df)}
.projects .section-title{color:var(--white);top:80px}
.projects p{position:absolute;left:210px;width:780px;top:130px;text-align:center;font-size:12px;line-height:24px;color:var(--white)}
.btn-outline{position:absolute;left:484px;top:234px;width:232px;height:46px;border:2px solid rgba(255,255,255,.85);color:var(--white);font-size:12px;font-weight:700;text-align:center;line-height:42px;text-transform:uppercase}
.news-card{position:absolute;top:2110px;width:494px;height:192px;border:1px solid var(--line);background:var(--white)}
.news-thumb{position:absolute;left:8px;top:12px;width:158px;height:166px}
.news-card h4{position:absolute;left:184px;top:24px;font-size:14.5px;font-weight:700;color:var(--navy);text-transform:uppercase}
.news-card p{position:absolute;left:184px;top:54px;width:296px;font-size:11.5px;line-height:22px;color:var(--muted)}
.btn-fill{position:absolute;left:184px;top:136px;width:100px;height:34px;background:var(--sky);color:var(--white);font-size:11.5px;font-weight:500;text-align:center;line-height:34px;text-transform:uppercase;border-radius:2px}
.testimonial{position:absolute;left:0;top:2348px;width:1200px;height:282px;background:var(--pale)}
.quote{position:absolute;left:175px;top:72px;width:540px;font-size:12px;line-height:23px;color:#555}
.quote-mark{position:absolute;font-family:Georgia,serif;font-size:34px;color:#b9bec4}
.author{position:absolute;left:175px;top:192px;font-size:14px;font-weight:700;color:var(--sky);text-transform:uppercase}
.author-date{position:absolute;left:175px;top:214px;font-size:12px;color:var(--muted)}
.portrait{position:absolute;left:772px;top:40px;width:200px;height:200px;border-radius:50%;border:5px solid #e2e4e7;background:linear-gradient(160deg,#c9a88c,#7a5038 70%,#5c3c2a)}
.site-footer{position:absolute;left:0;top:2630px;width:1200px;height:273px;background:var(--white);font-family:'Open Sans',sans-serif}
.site-footer .brand{left:95px;top:120px;font-size:36px}
.site-footer .brand-mark{width:48px;height:48px}
.foot-col{position:absolute;top:50px}
.foot-col h5{font-family:'Roboto',sans-serif;font-size:14px;font-weight:500;color:#333;text-transform:uppercase;margin-bottom:22px}
.contact-list li{list-style:none;display:flex;gap:12px;font-size:11.5px;line-height:16px;color:#444;margin-bottom:12px}
.contact-list svg{flex:none;margin-top:1px}
.foot-col p{font-size:12px;line-height:20px;color:#444}
.email-field{width:212px;height:34px;border:1px solid #cfd3d8;margin-top:18px;font-size:11.5px;color:#666;line-height:32px;padding-left:12px}
.btn-sub{margin-top:12px;width:80px;height:26px;background:var(--sky);color:var(--white);font-size:10px;font-weight:600;text-align:center;line-height:26px;text-transform:uppercase}
.socials{display:flex;gap:8px;margin-top:20px}
.socials span{width:36px;height:36px;border:1.5px solid #9aa1a8;border-radius:50%}
.copyright{position:absolute;left:0;top:2903px;width:1200px;height:67px;background:var(--navy-deep);color:var(--white);font-family:'Open Sans',sans-serif;font-size:12px;text-align:center;line-height:34px}
</style>
</head>
<body>

<header class="site-header">
  <div class="brand"><span class="brand-mark"></span>Quorvane</div>
  <nav class="main-nav">
    <span class="active" style="left:598px">Home</span>
    <span style="left:674px">About</span>
    <span style="left:756px">Services</span>
    <span style="left:855px">Blog</span>
    <span style="left:927px">Testimonial</span>
    <span style="left:1053px">Contact</span>
  </nav>
</header>

<svg class="hero" width="1200" height="670" viewBox="0 0 1200 670">
  <defs>
    <linearGradient id="heroFill" x1="0" y1="0" x2="1" y2="1">
      <stop offset="0" stop-color="#d8b08a"/>
      <stop offset=".4" stop-color="#5a7390"/>
      <stop offset=".75" stop-color="#26354a"/>
      <stop offset="1" stop-color="#4d6b86"/>
    </linearGradient>
  </defs>
  <path role="img" aria-label="Photo of a hand with a stylus over a tablet showing business charts" d="M0 0H1200V505C1000 660 350 720 0 335Z" fill="url(#heroFill)"/>
  <path d="M250 540C500 700 900 690 1200 515" fill="none" stroke="var(--sky)" stroke-width="10"/>
  <circle cx="1155" cy="436" r="7" fill="none" stroke="#fff" stroke-width="2"/>
  <circle cx="1155" cy="463" r="7" fill="none" stroke="var(--sky)" stroke-width="2"/>
  <circle cx="1155" cy="490" r="7" fill="none" stroke="#fff" stroke-width="2"/>
</svg>

<h2 class="section-title" style="top:792px">OUR <em>SERVICES</em></h2>
<p class="lead" style="top:834px">At vero eos et accusamus et iusto odio dignissimos ducimus qui blanditiis praesentium voluptatum deleniti atque corrupti quos dolores et quas molestias excepturi sint occaecati cupiditate non provident</p>

<div class="service" style="left:104px;top:920px">
  <svg width="120" height="120" viewBox="0 0 120 120"><circle cx="60" cy="60" r="58" fill="var(--navy)"/><circle cx="60" cy="60" r="52" fill="none" stroke="#fff" stroke-width="1.5"/><rect x="36" y="46" width="48" height="34" rx="3" fill="#fff"/><rect x="50" y="38" width="20" height="10" rx="2" fill="none" stroke="#fff" stroke-width="4"/><rect x="36" y="60" width="48" height="3" fill="var(--navy)"/></svg>
  <h3>Business</h3>
  <p>At vero eos et accusamus et iusto odio dignissimos ducimus qui blanditiis pra esentium voluptatum</p>
</div>
<div class="service" style="left:354px;top:920px">
  <svg width="120" height="120" viewBox="0 0 120 120"><circle cx="60" cy="60" r="58" fill="var(--sky)"/><circle cx="60" cy="60" r="52" fill="none" stroke="#fff" stroke-width="1.5"/><path d="M40 56a21 21 0 0 1 36-12M80 64a21 21 0 0 1-36 12" fill="none" stroke="#fff" stroke-width="6"/><path d="M72 36l10 6-10 8zM48 84l-10-6 10-8z" fill="#fff"/></svg>
  <h3>Process</h3>
  <p>At vero eos et accusamus et iusto odio dignissimos ducimus qui blanditiis pra esentium voluptatum</p>
</div>
<div class="service" style="left:606px;top:920px">
  <svg width="120" height="120" viewBox="0 0 120 120"><circle cx="60" cy="60" r="58" fill="var(--navy)"/><circle cx="60" cy="60" r="52" fill="none" stroke="#fff" stroke-width="1.5"/><path d="M36 52l24-10 24 10v26l-24 12-24-12z" fill="#fff"/><path d="M60 62v28M36 52l24 10 24-10" fill="none" stroke="var(--navy)" stroke-width="2"/><path d="M60 26l10 12h-6v10h-8V38h-6z" fill="#fff"/></svg>
  <h3>Outsourcing</h3>
  <p>At vero eos et accusamus et iusto odio dignissimos ducimus qui blanditiis pra esentium voluptatum</p>
</div>
<div class="service" style="left:860px;top:920px">
  <svg width="120" height="120" viewBox="0 0 120 120"><circle cx="60" cy="60" r="58" fill="var(--navy)"/><circle cx="60" cy="60" r="52" fill="none" stroke="#fff" stroke-width="1.5"/><circle cx="60" cy="56" r="14" fill="#fff"/><rect x="53" y="68" width="14" height="12" rx="2" fill="#fff"/><path d="M60 32v-6M38 56h-6M88 56h-6M44 40l-4-4M76 40l4-4" stroke="#fff" stroke-width="3"/></svg>
  <h3>Solutions</h3>
  <p>At vero eos et accusamus et iusto odio dignissimos ducimus qui blanditiis pra esentium voluptatum</p>
</div>

<section class="welcome">
  <h2 class="welcome-title">WELCOME TO <em>QUORVANE</em></h2>
  <div class="welcome-text">
    <p>Contrary to popular belief, Lorem Ipsum is not simply random text. It has roots in a piece of classical Latin literature from 45 BC, making it over 2000 years old. Tobias Wrenfield, a Latin professor at Larkmoor College in Eastvale, looked up one of the more obscure Latin words, consectetur, from a Lorem Ipsum passage, and going through the cites of the word in classical the undoubtable source. Lorem Ipsum comes from sections</p>
    <p>There are many variations of passages of Lorem Ipsum available, but the majority have suffered alteration in some form, by injected humour, or randomised words which don't look even slightly thing embarrassing hidden in the middle of text. All the Lorem Ipsum generators</p>
  </div>
  <div class="devices" role="img" aria-label="Desktop monitor and tablet showing the website"></div>
</section>

<section class="projects">
  <h2 class="section-title">OUR PROJECTS</h2>
  <p>Steel framing and any type of finishing or millwork.Sed ut perspiciatis unde omnis iste natus error sit volupt atem accusantium  consequuntur magnidolores eos qui ratione voluptatem sequi nesciunt.Sed ut perspiciatis unde omnis iste natus error sit voluptatem accusantium doloremque laudantiumdolores eos qui ratione voluptatem sequi nesciunt.Sed</p>
  <div class="btn-outline">Click here for more info</div>
</section>

<h2 class="section-title" style="top:1988px">LATEST <em>NEWS</em></h2>
<p class="lead" style="top:2034px;left:240px;width:720px">Sed ut perspiciatis unde omnis iste natus error sit voluptatem accusantium doloremque laudantium, totam rem aperiam, eaque illo inventore veritatis et quasi architecto beatae vitae dicta sunt explicabo.</p>

<article class="news-card" style="left:88px">
  <div class="news-thumb" role="img" aria-label="Photo of a business handshake over a desk" style="background:linear-gradient(135deg,#e6d6bf,#9c8466 60%,#4d4032)"></div>
  <h4>Contrary to popular belief</h4>
  <p>Sed ut perspiciatis unde omnis iste natus error sit volu ptatem accusantium doloremque laudantium, totam rem to beatae vitae dicta sunt explicabo.</p>
  <div class="btn-fill">Read more</div>
</article>
<article class="news-card" style="left:620px">
  <div class="news-thumb" role="img" aria-label="Photo of a businessman touching a digital network screen" style="background:linear-gradient(135deg,#9fb6cc,#3d5e80 55%,#1c2b40)"></div>
  <h4>Contrary to popular belief</h4>
  <p>Sed ut perspiciatis unde omnis iste natus error sit volu ptatem accusantium doloremque laudantium, totam rem to beatae vitae dicta sunt explicabo.</p>
  <div class="btn-fill">Read more</div>
</article>

<section class="testimonial">
  <span class="quote-mark" style="left:155px;top:40px">&ldquo;</span>
  <p class="quote">Sed ut perspiciatis unde omnis iste natus error sit voluptatem accusantium doloremque laudantium, totam rem aperiam, eaque ipsa quae ab illo inventore veritatis et quasi architecto beatae vitae dicta sunt explicabo. Nemo enim ipsam voluptatem quia voluptas sit aspernatur aut odit aut fugit, sed quia consequuntur magni dolores eos qui ratione voluptatem sequi nesciunt.</p>
  <span class="quote-mark" style="left:560px;top:146px">&rdquo;</span>
  <div class="author">Mara Ellison</div>
  <div class="author-date">Posted On 07 July 2016</div>
  <div class="portrait" role="img" aria-label="Portrait photo of a smiling client"></div>
</section>

<footer class="site-footer">
  <div class="brand"><span class="brand-mark"></span>Quorvane</div>
  <div class="foot-col" style="left:392px">
    <h5>Contact Us</h5>
    <ul class="contact-list">
      <li><svg width="12" height="12" viewBox="0 0 12 12"><path d="M2 1h3l1 3-2 1a7 7 0 0 0 3 3l1-2 3 1v3c-6 1-10-3-9-9z" fill="#666"/></svg>(000)-555-0142 (Phone)</li>
      <li><svg width="12" height="12" viewBox="0 0 12 12"><rect x="1" y="4" width="10" height="7" fill="#666"/><rect x="3" y="1" width="6" height="4" fill="none" stroke="#666"/></svg>(000)-555-0143 (Fax)</li>
      <li><svg width="12" height="12" viewBox="0 0 12 12"><rect x="1" y="2" width="10" height="8" fill="#666"/><path d="M1 2l5 4 5-4" fill="none" stroke="#fff"/></svg><u>info@quorvane.com</u></li>
      <li><svg width="12" height="12" viewBox="0 0 12 12"><path d="M6 11L2 5a4 4 0 1 1 8 0z" fill="#666"/><circle cx="6" cy="4.5" r="1.5" fill="#fff"/></svg># 356 Lorem Ipsum Dummy<br>Lorem Ipsum</li>
    </ul>
  </div>
  <div class="foot-col" style="left:624px;width:230px">
    <h5>Newsletter</h5>
    <p>Register Your email address to get information about us</p>
    <div class="email-field">Email Address</div>
    <div class="btn-sub">Subscribe</div>
  </div>
  <div class="foot-col" style="left:885px;width:220px">
    <h5>Follow Us</h5>
    <p style="font-size:11.5px;line-height:19px">Lorem ipsum dolor sit amet, conse ctetur adipiscing elit. Nulla in purus nibh. Donec ornare</p>
    <div class="socials"><span></span><span></span><span></span><span></span><span></span></div>
  </div>
</footer>

<div class="copyright">&copy; Copyright 2016 Quorvane .All Rights Reserved</div>

</body>
</html>
```